Tidewell Home & Business Heating & Pipework, needs a business card Design

We need a business card design for a company in the United Kingdom, we work mainly in London in Domestic Plumbing & Heating and would like to branch out (more) in to the Commercial aspect of the business.
We need the card to promote care, trust, professionalism, because we do, if possible, we will always better or match prices with an over all better experience for clients.

Info to add on card...

My name... Dorian Welk
Cell... 07491365817
Email... dorianwelk00@Postrun.com
Business/Post code... NW18 4TB

Thanks

Dorian

Hi there updated my design project! If you could please look through again and add as much as possable (as you will see) I'd be very grateful! Although I do enjoy seeing all your fantastic designs, I don't want to spend the remaining 14 days being hard to please. PS.. I'm from NZ but living in UK, if you find patriotic (NZ) that is do add in. Not of huge importance but It dose get peoples attention! Thanks a lot, Dorian

I work in Chelsea and most of my days so think Chelsea.

Thanks.

Business

Serif
Sans Serif

• Just want text to be as easy to read as possible!

Would like to see some or all pictures I have on the card if at all possible.
They are well known logos in my industry.
And my team and I are all fully qualified in these different schemes.

Also a break down of services I provide!

- Central Heating Engineering.
- Bathroom and Kitchen Fitting.
- Plumbing.
- Electrical.
- Tiling.
- All Your Carpentry and Building Needs.

Thanks.

• Only restriction no pink otherwise go for it!

Thanks.

```html
<!DOCTYPE html>
<html lang="en">
<head>
<meta charset="utf-8">
<title>Tidewell Home &amp; Business Heating &amp; Pipework – Business Card</title>
<link rel="stylesheet" href="https://fonts.googleapis.com/css2?family=Jura:wght@500;600&display=swap">
<style>
  :root {
    --page-bg: #eceef0;
    --card-white: #ffffff;
    --brand-blue: #1a7fcc;
    --brand-blue-deep: #0d63b3;
    --brand-blue-light: #2a95dc;
    --brand-green: #6cc04a;
    --brand-green-light: #9ad64f;
    --edge-grey: #d9dee2;
    --text-light: #ffffff;
    --logo-text: #1e88c9;
  }
  * { margin: 0; padding: 0; box-sizing: border-box; }
  html, body {
    width: 1200px; height: 800px; overflow: hidden;
    background: var(--page-bg);
    font-family: "Jura", "Segoe UI", sans-serif;
  }
  .card {
    position: absolute; left: 100px; top: 100px;
    width: 1000px; height: 600px;
    background: var(--card-white);
    box-shadow: 0 10px 30px rgba(0,0,0,0.15);
    overflow: hidden;
  }
  .card-shapes { position: absolute; inset: 0; }
  .brand {
    position: absolute; left: 20px; top: 210px; width: 360px;
    text-align: center; color: var(--logo-text);
  }
  .brand-dot {
    width: 64px; height: 64px; border-radius: 50%;
    background: var(--logo-text); margin: 0 auto 24px;
  }
  .brand-name {
    font-size: 23px; font-weight: 600; line-height: 1.3;
    letter-spacing: 0.5px; white-space: nowrap;
  }
  .details {
    position: absolute; right: 50px; top: 60px; width: 460px;
    text-align: right; color: var(--text-light);
  }
  .person-name { font-size: 36px; font-weight: 600; letter-spacing: 3px; text-transform: uppercase; }
  .person-role { font-size: 22px; font-weight: 600; letter-spacing: 2px; text-transform: uppercase; margin-top: 4px; margin-right: 4px; }
  .address { font-size: 27px; font-weight: 600; line-height: 1.35; margin-top: 70px; }
  .contacts { list-style: none; margin-top: 62px; }
  .contacts li {
    display: flex; justify-content: flex-end; align-items: center;
    font-size: 21px; font-weight: 600; letter-spacing: 1px; height: 36px;
    white-space: nowrap;
  }
  .contacts svg { width: 22px; height: 22px; margin-left: 14px; flex: none; }
</style>
</head>
<body>
  <div class="card">
    <svg class="card-shapes" viewBox="0 0 1000 600" width="1000" height="600" aria-hidden="true">
      <defs>
        <linearGradient id="blueFill" x1="0" y1="0" x2="1" y2="1">
          <stop offset="0" stop-color="var(--brand-blue-deep)"/>
          <stop offset="0.5" stop-color="var(--brand-blue-light)"/>
          <stop offset="1" stop-color="var(--brand-blue)"/>
        </linearGradient>
        <linearGradient id="greenFill" x1="0" y1="0" x2="0" y2="1">
          <stop offset="0" stop-color="var(--brand-green)"/>
          <stop offset="1" stop-color="var(--brand-green-light)"/>
        </linearGradient>
      </defs>
      <path d="M365 0 C490 190 420 440 215 600" fill="none" stroke="var(--edge-grey)" stroke-width="14"/>
      <path d="M385 0 H540 C560 230 440 440 250 600 H235 C430 440 500 200 385 0 Z" fill="url(#greenFill)"/>
      <path d="M540 0 H1000 V600 H250 C470 450 580 240 540 0 Z" fill="url(#blueFill)"/>
    </svg>

    <div class="brand">
      <div class="brand-dot"></div>
      <p class="brand-name">Tidewell Home &amp; Business<br>Heating &amp; Pipework</p>
    </div>

    <div class="details">
      <h1 class="person-name">Dorian Welk</h1>
      <p class="person-role">Financial Advisor</p>
      <p class="address">NW18 4TB, Chelsea<br>Works Road London</p>
      <ul class="contacts">
        <li>07491 365817
          <svg viewBox="0 0 24 24" fill="#fff"><path d="M6.6 10.8a15 15 0 0 0 6.6 6.6l2.2-2.2c.3-.3.7-.4 1-.2 1.1.4 2.3.6 3.6.6.6 0 1 .4 1 1V20c0 .6-.4 1-1 1A17 17 0 0 1 3 4c0-.6.4-1 1-1h3.5c.6 0 1 .4 1 1 0 1.3.2 2.5.6 3.6.1.3 0 .7-.2 1z"/></svg>
        </li>
        <li>07491 365817
          <svg viewBox="0 0 24 24" fill="none" stroke="#fff" stroke-width="2"><rect x="6" y="2" width="12" height="20" rx="2"/><line x1="11" y1="18" x2="13" y2="18"/></svg>
        </li>
        <li>07491 365817
          <svg viewBox="0 0 24 24" fill="#fff"><rect x="3" y="8" width="18" height="13" rx="1"/><rect x="7" y="3" width="10" height="6" fill="none" stroke="#fff" stroke-width="2"/><rect x="6" y="11" width="12" height="2" fill="#1a7fcc"/><rect x="6" y="15" width="12" height="2" fill="#1a7fcc"/></svg>
        </li>
        <li>dorianwelk00@Postrun.com
          <svg viewBox="0 0 24 24" fill="none" stroke="#fff" stroke-width="2"><rect x="2" y="5" width="20" height="14"/><path d="M2 5l10 8 10-8"/></svg>
        </li>
        <li>www.tidewellheat.co.uk
          <svg viewBox="0 0 24 24" fill="none" stroke="#fff" stroke-width="1.8"><circle cx="12" cy="12" r="10"/><ellipse cx="12" cy="12" rx="4.5" ry="10"/><line x1="2" y1="12" x2="22" y2="12"/><path d="M4 7h16M4 17h16"/></svg>
        </li>
      </ul>
    </div>
  </div>
</body>
</html>
```